Northfield Builders Guild Business card

We are looking for a new business card design with photo included.
Our business is a nonprofit construction contractor membership organization. We offer business education, assist with business setup and licensing, provide safety training, and provide a member directory.
URL: www.builderslinkguild.org
Color code:
CMYK: 0 cyan, 42 magenta, 100 yellow, 0 black for Print.
Hexidecimal: #FF9900
RGB: R 255; G 153; B 0

```html
<!DOCTYPE html>
<html lang="en">
<head>
<meta charset="utf-8">
<title>Northfield Builders Guild – Business Card</title>
<link href="https://fonts.googleapis.com/css2?family=Open+Sans:wght@400;600;800&display=swap" rel="stylesheet">
<style>
  :root {
    --brand-orange: #ff9900;
    --band-orange: #f7941d;
    --ink-dark: #333333;
    --ink-body: #444444;
    --card-white: #ffffff;
    --backdrop: #e9e6e1;
  }
  * { box-sizing: border-box; margin: 0; padding: 0; }
  html, body { width: 1200px; height: 911px; overflow: hidden; }
  body {
    background: var(--backdrop);
    font-family: "Open Sans", Arial, sans-serif;
    position: relative;
  }
  .card {
    position: absolute;
    width: 520px;
    height: 297px;
    background: var(--card-white);
    box-shadow: 0 6px 18px rgba(0,0,0,0.18);
    overflow: hidden;
  }
  .card--front { left: 45px; top: 307px; }
  .card--back { left: 635px; top: 307px; }

  .wordmark {
    font-weight: 800;
    color: var(--ink-dark);
    text-transform: uppercase;
    line-height: 1;
    letter-spacing: 0.5px;
  }
  .card--front .wordmark {
    position: absolute; left: 34px; top: 36px;
    font-size: 22px; width: 210px;
  }
  .card--back .wordmark {
    position: absolute; left: 0; right: 0; top: 50%;
    transform: translateY(-50%);
    text-align: center; font-size: 30px;
  }

  .holder { position: absolute; left: 34px; top: 110px; }
  .holder__name {
    color: var(--brand-orange);
    font-size: 15px; font-weight: 400; letter-spacing: 3px;
    text-transform: uppercase;
  }
  .holder__title { color: var(--ink-body); font-size: 10px; margin-top: 1px; }

  .contacts { position: absolute; left: 34px; top: 160px; list-style: none; }
  .contacts li {
    display: flex; align-items: center; gap: 8px;
    font-size: 10.5px; color: var(--ink-body); height: 19px;
  }
  .contacts svg { width: 15px; height: 15px; flex: none; }

  .address {
    position: absolute; right: 26px; top: 26px;
    font-size: 9px; color: var(--ink-body); line-height: 1.35; text-align: left;
  }
  .bands { position: absolute; left: 0; bottom: 0; width: 520px; height: 44px; }
</style>
</head>
<body>
  <section class="card card--front" aria-label="Business card front">
    <div class="wordmark">Northfield Builders Guild</div>
    <div class="address">118 Alder Street Suite 210<br>Fairview MI 49011</div>
    <div class="holder">
      <div class="holder__name">Daniel Reyes</div>
      <div class="holder__title">CEO/Managing Director</div>
    </div>
    <ul class="contacts">
      <li>
        <svg viewBox="0 0 16 16"><circle cx="8" cy="8" r="7" fill="none" stroke="var(--brand-orange)" stroke-width="1.2"/><rect x="5.8" y="4" width="4.4" height="8" rx="0.8" fill="none" stroke="var(--brand-orange)" stroke-width="1.1"/></svg>
        555-014-2288
      </li>
      <li>
        <svg viewBox="0 0 16 16"><circle cx="8" cy="8" r="7" fill="none" stroke="var(--brand-orange)" stroke-width="1.2"/><path d="M4.5 6.5h7v4.5h-7z M6 6.5v-1.5h4v1.5" fill="var(--brand-orange)"/></svg>
        555-014-2288
      </li>
      <li>
        <svg viewBox="0 0 16 16"><circle cx="8" cy="8" r="7" fill="none" stroke="var(--brand-orange)" stroke-width="1.2"/><rect x="4.5" y="5.5" width="7" height="5" fill="var(--brand-orange)"/><path d="M4.5 5.5l3.5 3 3.5-3" fill="none" stroke="#fff" stroke-width="0.8"/></svg>
        dreyes@northfieldmail.com
      </li>
      <li>
        <svg viewBox="0 0 16 16"><circle cx="8" cy="8" r="7" fill="none" stroke="var(--brand-orange)" stroke-width="1.2"/><circle cx="8" cy="8" r="3.8" fill="none" stroke="var(--brand-orange)" stroke-width="0.9"/><path d="M4.2 8h7.6 M8 4.2v7.6" stroke="var(--brand-orange)" stroke-width="0.8"/></svg>
        www.builderslinkguild.org
      </li>
    </ul>
    <svg class="bands" viewBox="0 0 520 44" preserveAspectRatio="none" aria-hidden="true">
      <polygon points="0,14 208,14 196,26 0,26" fill="var(--ink-dark)"/>
      <polygon points="0,30 190,30 214,14 520,14 520,44 0,44" fill="var(--band-orange)"/>
    </svg>
  </section>

  <section class="card card--back" aria-label="Business card back">
    <div class="wordmark">Northfield<br>Builders Guild</div>
  </section>
</body>
</html>
```